Tri-Fold Brochure for Christian Author and Speaker

Lorna Whitfield is an inspirational author and speaker, sharing her testimony and encouraging others in their walk with Christ. A gifted writer, her work has been featured on Gently Radiant, Steadfast Mornings, and Hymns & Teacups Magazine (Fall 2011).

Lorna ‘s first book, Leaving the Lantern Room: Unmasking Hidden Snares in Ordinary Living, is an informative memoir and Bible study, recounting her journey from committed Christian to witch, medium, and ghost hunter for eight years until restored to faith in Jesus Christ. She was a contributing author to Walking Past the Shadows: A Candid View of Sorcery from Those Who Left by Dale Pennington and a consultant for the novel The Keeper of Marlow Hollow by Beacon Prize Winning Author, Helen Osgood.

Lorna’s second book, An Insider’s Guide to Spiritual Warfare: 20 Battle-Tested Strategies from Behind Enemy Lines, will be published by Harvest Lane Press for Fall 2014.

Lorna is a wife and mother. She enjoys writing, spending time with her family, taking long walks, listening to music of all kinds, and experiencing God’s daily gift called life.

You can read more about Lorna and see the look and feel we are going for at www.lornawhitfield.example

The brochure is to be used as a promotional tool to gain Lorna speaking engagements. You can see the topics she covers at http://www.lornawhitfield.example/speaking-engagements/.

More info can be found at: https://www.facebook.com/AuthorLornaWhitfield
https://www.facebook.com/VMUCX
https://www.facebook.com/LeavingtheLanternRoom
https://www.facebook.com/OpenDoorOutreach
http://www.opendooroutreach.example

I have uploaded 3 headshots, book covers for both of Lorna's books and the design layout in .EPS format from Swiftprintery.example where I will be getting printing done.

3 more days till the contest ends get your final designs in.

Reason: I'm extending this as I am tied up at a leadership conference and will not be able to give this the attention it deserves till the weekend.

Target Market(s)

Churches and women's groups. Lorna's current audience skews heavy to women on a 70/30 ratio.

Industry/Entity Type

Christian

Requirements
Must have
• Headshot I have uploaded 3
Quotes from previous speaking engagements you can find those at http://www.lornawhitfield.example/speaking-engagements/

```html
<!DOCTYPE html>
<html lang="en">
<head>
<meta charset="utf-8">
<title>Testimony – Lorna Whitfield</title>
<link rel="stylesheet" href="https://fonts.googleapis.com/css2?family=Jost:wght@400;700&family=Cinzel:wght@400&display=swap">
<style>
  :root {
    --rose: #e34f70;
    --rose-light: #f07a95;
    --rose-deep: #d23d61;
    --white: #ffffff;
    --photo-dark: #4d4038;
    --photo-mid: #8b8a78;
    --photo-light: #b8b9a8;
  }
  html, body {
    margin: 0;
    padding: 0;
    overflow: hidden;
    background: var(--white);
  }
  .page {
    position: relative;
    width: 848px;
    height: 1200px;
    overflow: hidden;
    background: var(--rose);
    color: var(--white);
    font-family: "Jost", "Century Gothic", sans-serif;
  }
  .floral-backdrop {
    position: absolute;
    inset: 0;
    background:
      radial-gradient(ellipse 420px 360px at 200px 250px, rgba(255,160,185,0.35), transparent 70%),
      radial-gradient(ellipse 380px 420px at 600px 1000px, rgba(255,170,190,0.35), transparent 70%),
      radial-gradient(ellipse 300px 260px at 760px 120px, rgba(255,150,175,0.25), transparent 70%),
      linear-gradient(160deg, var(--rose-light) 0%, var(--rose) 45%, var(--rose-deep) 100%);
  }
  .testimony-title {
    position: absolute;
    left: 71px;
    top: 256px;
    margin: 0;
    font-weight: 700;
    font-size: 45px;
    letter-spacing: 0.5px;
    line-height: 1;
  }
  .testimony-body {
    position: absolute;
    left: 71px;
    top: 333px;
    width: 386px;
    margin: 0;
    font-size: 16.2px;
    line-height: 23.3px;
    text-align: justify;
  }
  .testimony-body strong { font-weight: 700; }
  .headshot-frame {
    position: absolute;
    left: 472px;
    top: 346px;
    width: 311px;
    height: 461px;
    box-sizing: border-box;
    border: 5px solid var(--white);
    background: var(--white);
  }
  .headshot {
    width: 100%;
    height: 100%;
    background:
      radial-gradient(ellipse 120px 200px at 55% 65%, var(--photo-dark), transparent 75%),
      linear-gradient(90deg, var(--photo-mid) 0%, var(--photo-light) 45%, var(--photo-mid) 100%);
  }
  .signature {
    position: absolute;
    left: 0;
    width: 100%;
    top: 1058px;
    text-align: center;
  }
  .author-name {
    margin: 0;
    font-family: "Cinzel", "Trajan Pro", serif;
    font-weight: 400;
    font-size: 29px;
    line-height: 31px;
    letter-spacing: 1px;
  }
  .author-site {
    margin: 22px 0 0;
    font-size: 15.5px;
    letter-spacing: 0.3px;
  }
</style>
</head>
<body>
  <main class="page">
    <div class="floral-backdrop" role="img" aria-label="Soft pink lily flowers decorating the background"></div>

    <h1 class="testimony-title">Testimony</h1>

    <p class="testimony-body">I was raised in a traditional <strong>Christian home</strong>. One of my earliest memories of church is sitting on a hard wooden pew with my mother listening to a pipe organ play a traditional hymn. We were attending a Methodist church at the time. I remember hearing Bible stories, singing songs about the B.I.B.L.E and Jesus Loving the Little Children. It wasn’t until I was six years old attending Vacation Bible School that I learned how Jesus wanted to save me from my sins. I can’t say I understood the greater concept of sin but I did want Jesus to be my friend. At the end of the lesson, I raised my hand and the teacher prayed with me to “accept Jesus into my heart”. However, as I went to church each Sunday, sang those Bible songs, and learned about God, there were other influences in my life. Even as a young child I was aware of a hidden world surrounding us because I could feel the beings present within it. I could sense a dark being in the corner of my room, watching me as I played with my dolls.</p>

    <div class="headshot-frame">
      <div class="headshot" role="img" aria-label="Headshot of Lorna Whitfield standing beside a tree trunk, arms crossed, in a brown lace top"></div>
    </div>

    <footer class="signature">
      <p class="author-name">Lorna<br>Whitfield</p>
      <p class="author-site">www.lornawhitfield.example</p>
    </footer>
  </main>
</body>
</html>
```